Exclusive beauty salon needs a price list or services booklet

I need a new very attractive flyer for my beauty salon, containing information on the different services and their prices.
In attachment you can find a pdf of the "old" one, but I'd love to have a beautifully designed new one!
I'd love to have a booklet in format 148 x 148 mm, or in US format, containing 12 or 16 pages, but if you can offer other nice looking designs they are welcome!
The services that need to come in the booklet with their prices can all be found on my website: www.atelierverano.be, starting with
Gelaatsverzorging
Wimperverlenging
Suikerontharing
Wimperlifting
Permanente Make Up
Airbrush Tanning

Target Market(s)

woman from 20 to 89 years old

Industry/Entity Type

Beauty Salon

Font styles to use
Sans Serif

Colors

Designer to choose colors to be used in the design.

Requirements
Must have
• a classy nice look, it must contain details about the services from my beauty salon and their prices, and nice pictures.
• The Names, prices and explanations of the services can easily be found on my website: www.atelierverano.be
Nice to have
• In attachment you can find the "old" price list in pdf, what I need now is a "new booklet" with the new logo and updated services price list.
• I need a very nice and attractive looking booklet, classy chique, Paris chique, looking very expensive.
Should not have
• Not too much colors, not too curly, but still feminine

```html
<!DOCTYPE html>
<html lang="nl">
<head>
<meta charset="utf-8">
<title>Ontharing met suiker – prijslijst</title>
<link rel="stylesheet" href="https://fonts.googleapis.com/css2?family=Raleway:wght@300;400;500;600&display=swap">
<style>
  :root {
    --backdrop: #e4e4e4;
    --paper: #ffffff;
    --pink: #e3bcc2;
    --pink-text: #e08a99;
    --blue: #a8d8e2;
    --blue-text: #8cc8d8;
    --body-text: #7a7a7a;
    --photo-warm: #caa587;
    --photo-light: #f1e3d6;
    --ink: #555555;
  }
  * { box-sizing: border-box; margin: 0; padding: 0; }
  html, body { width: 1200px; height: 523px; overflow: hidden; }
  body {
    background: var(--backdrop);
    font-family: "Raleway", Arial, sans-serif;
    position: relative;
  }
  .spread {
    position: absolute;
    left: 120px; top: 21px;
    width: 960px; height: 481px;
    display: flex;
    box-shadow: 0 4px 14px rgba(0,0,0,.12);
  }
  .page {
    position: relative;
    width: 480px; height: 481px;
    background: var(--paper);
    overflow: hidden;
  }
  .page--left { border-right: 1px solid #ececec; }

  .photo {
    position: absolute; left: 0; top: 0;
    width: 230px; height: 100%;
    background: linear-gradient(90deg, var(--photo-warm) 0%, var(--photo-light) 55%, rgba(255,255,255,0) 100%);
  }
  .intro {
    position: absolute; left: 205px; top: 22px; width: 255px;
  }
  .intro__title {
    text-align: right;
    color: var(--blue-text);
    font-weight: 400;
    font-size: 17px;
    letter-spacing: .5px;
    margin-bottom: 10px;
  }
  .intro__lead {
    color: var(--pink-text);
    font-size: 12px;
    line-height: 1.35;
    font-weight: 500;
    margin-bottom: 14px;
  }
  .benefits__heading {
    color: var(--ink);
    font-size: 8.5px;
    font-weight: 600;
    margin-bottom: 9px;
  }
  .benefits { list-style: none; }
  .benefits li {
    position: relative;
    padding-left: 9px;
    color: var(--body-text);
    font-size: 8.2px;
    line-height: 1.4;
    margin-bottom: 10px;
  }
  .benefits li::before {
    content: "";
    position: absolute; left: 0; top: 4px;
    width: 3px; height: 3px; border-radius: 50%;
    background: var(--pink-text);
  }

  .prices { position: absolute; left: 28px; top: 40px; right: 0; list-style: none; }
  .price-row {
    display: flex; justify-content: space-between; align-items: center;
    height: 19px; margin-bottom: 9px;
    padding: 0 40px 0 15px;
    color: #fff;
    font-size: 12px;
    letter-spacing: .6px;
    text-transform: uppercase;
  }
  .price-row:nth-child(odd) { background: var(--pink); }
  .price-row:nth-child(even) { background: var(--blue); }
  .price-row__amount { font-size: 9px; font-weight: 600; }

  .brand {
    position: absolute; right: 22px; bottom: 24px;
    display: flex; align-items: center; gap: 6px;
    color: var(--ink);
    font-size: 9px;
    letter-spacing: 2px;
    text-transform: uppercase;
  }
  .brand__mark { width: 8px; height: 8px; border: 1px solid var(--ink); }
</style>
</head>
<body>
  <div class="spread">
    <section class="page page--left">
      <div class="photo" role="img" aria-label="Foto van gladde vrouwenbenen en heup in warme huidtinten"></div>
      <div class="intro">
        <h1 class="intro__title">ONTHARING MET SUIKER</h1>
        <p class="intro__lead">Heb je ook genoeg van lichaams- en/of gezichtsbeharing maar ben je niet tevreden met het resultaat van scheren/harsen/laseren? Dan is ontharen met suiker van Verano's dé oplossing!</p>
        <p class="benefits__heading">De voordelen van ontharen met suiker:</p>
        <ul class="benefits">
          <li>De haren worden met de haargroeirichting verwijderd, hierdoor vermindert de pijn en je hebt geen last van haartjes die afbreken</li>
          <li>De haren worden volledig verwijderd (met de haarwortel) waardoor ze dunner en donziger worden en minder snel aangroeien</li>
          <li>Er wordt hygiënisch gewerkt</li>
          <li>De huidstructuur verbetert door het verwijderen van dode huidcellen zonder de levende cellen te beschadigen</li>
          <li>Suiker bestaat uit lichaamseigen stoffen waardoor de huid minder fel reageert op de ontharing.</li>
          <li>Suikerontharing zorgt ervoor dat de haargroei vermindert na iedere behandeling en verfijnt de haarstructuur</li>
          <li>met suikerontharing werkt men op lichaamstemperatuur dus geen brandwonden</li>
          <li>suikerontharing is geschikt voor de couperose huid en is uiterst geschikt voor de meest gevoelige plaatsen (bikini, gezicht,…)</li>
          <li>suiker is wateroplosbaar, dus geen ongewenste plakseltjes</li>
        </ul>
      </div>
    </section>

    <section class="page page--right">
      <ul class="prices">
        <li class="price-row"><span>Wenkbrauwen</span><span class="price-row__amount">€9</span></li>
        <li class="price-row"><span>Wenkbrauwen en bovenlip</span><span class="price-row__amount">€16</span></li>
        <li class="price-row"><span>Bovenlip of kin</span><span class="price-row__amount">€9</span></li>
        <li class="price-row"><span>Bovenlip en kin</span><span class="price-row__amount">€16</span></li>
        <li class="price-row"><span>Gezicht (bovenlip, kin, wangen en wenkbrauw)</span><span class="price-row__amount">€25</span></li>
        <li class="price-row"><span>Oksels</span><span class="price-row__amount">€12</span></li>
        <li class="price-row"><span>Armen</span><span class="price-row__amount">€20</span></li>
        <li class="price-row"><span>Brazilian bikini of string</span><span class="price-row__amount">€30</span></li>
        <li class="price-row"><span>Bikinilijn</span><span class="price-row__amount">€15</span></li>
        <li class="price-row"><span>Onderbeen en knie</span><span class="price-row__amount">€30</span></li>
        <li class="price-row"><span>Bovenbenen</span><span class="price-row__amount">€20</span></li>
        <li class="price-row"><span>Volledige benen (zonder bikini)</span><span class="price-row__amount">€50</span></li>
        <li class="price-row"><span>Volledige benen incl. bikinilijn</span><span class="price-row__amount">€59</span></li>
      </ul>
      <div class="brand"><span class="brand__mark"></span><span>Atelier Verano</span></div>
    </section>
  </div>
</body>
</html>
```